Business card for Luxury Portable Restroom Trailer company

We are a Luxury Portable Restroom Trailer Company Called FALCRIDGE HIRES. Based in Orange County California. We provide portable restroom trailers for events, such as, Weddings, Concerts, Charity events, Sporting events, Tournaments, Corporate events, ect. We rent and Sell the Luxury restrooms. Our colors are white, grey, and Orange. As you will see in the logo we uploaded.
There are 2 people in the company so the names and titles will change for the 3 people but card will remain the same. Here is the information for each Person: Dwight Penner CFO 555 318-0476
next Person: Leon Marchetti VP 555 318-0476
Next Person: Owen Marchetti CEO 555 318-0476
Information to include on the card: Luxury Restroom Trailers Rental and Sales. Weddings, Concerts, Charity, Sporting and Corp. Events.

```html
<!DOCTYPE html>
<html lang="en">
<head>
<meta charset="utf-8">
<title>Falcridge Hires – Business Card</title>
<link href="https://fonts.googleapis.com/css2?family=Open+Sans:wght@400;600;700&display=swap" rel="stylesheet">
<style>
  :root {
    --stage: #232323;
    --card-dark: #2a2a2e;
    --band-1: #242428;
    --band-2: #1e1e21;
    --orange: #f26522;
    --grey-text: #6f6f73;
    --white: #ffffff;
    --light: #e6e6e6;
    --pattern-a: #8a8a8a;
    --pattern-b: #4a4a4a;
  }
  * { margin: 0; padding: 0; box-sizing: border-box; }
  html, body {
    width: 1200px; height: 768px; overflow: hidden;
    background: var(--stage);
    font-family: "Open Sans", sans-serif;
  }
  .stage {
    position: relative; width: 1200px; height: 768px;
    display: flex; justify-content: center; align-items: center; gap: 60px;
  }
  .card {
    position: relative; width: 320px; height: 540px;
    border-radius: 22px; overflow: hidden;
    box-shadow: 0 18px 40px rgba(0,0,0,.55);
  }

  /* Back side */
  .card-back .pattern-fill {
    position: absolute; inset: 0;
    background: linear-gradient(160deg, var(--pattern-a) 0%, #6a6a6a 45%, var(--pattern-b) 100%);
  }
  .card-back .back-brand {
    position: absolute; top: 36px; right: 54px;
    display: flex; align-items: center; gap: 10px;
    writing-mode: vertical-rl; transform: rotate(180deg);
    padding: 12px 8px; background: rgba(42,42,46,.55);
  }
  .brand-name {
    font-family: "Open Sans", sans-serif; font-weight: 700;
    color: var(--orange); letter-spacing: 1px; white-space: nowrap;
  }
  .card-back .brand-name { font-size: 20px; }
  .brand-mark { width: 12px; height: 12px; background: var(--orange); }

  /* Front side */
  .card-front { background: var(--card-dark); }
  .card-front .bands { position: absolute; inset: 0; }
  .front-brand {
    position: absolute; top: 44px; left: 0; right: 0;
    display: flex; justify-content: center; align-items: center; gap: 10px;
  }
  .front-brand .brand-name { font-size: 24px; }
  .person {
    position: absolute; top: 196px; left: 0; right: 0; text-align: center;
  }
  .person-name { font-size: 26px; font-weight: 700; line-height: 1.1; }
  .person-name .first { color: var(--orange); }
  .person-name .last { color: var(--grey-text); }
  .person-title { color: var(--white); font-size: 15px; font-weight: 600; margin-top: 4px; }
  .contact-icons { display: flex; justify-content: center; gap: 8px; margin-top: 12px; }
  .contact-icons svg { width: 26px; height: 26px; }
  .contact-lines { margin-top: 10px; color: var(--white); font-size: 15px; line-height: 1.45; }
  .services {
    position: absolute; left: 24px; right: 20px; bottom: 34px;
    color: var(--light); font-size: 13.5px; line-height: 1.7;
  }
  .services li { list-style: none; display: inline; margin-right: 10px; white-space: nowrap; }
  .services li::before {
    content: ""; display: inline-block; width: 8px; height: 8px; border-radius: 50%;
    background: var(--orange); margin-right: 5px; vertical-align: 1px;
  }
</style>
</head>
<body>
<main class="stage">
  <section class="card card-back" aria-label="Card back">
    <div class="pattern-fill" role="img" aria-label="Repeating brand-mark pattern in metallic grey tones"></div>
    <div class="back-brand">
      <span class="brand-mark"></span>
      <span class="brand-name">FALCRIDGE HIRES</span>
    </div>
  </section>

  <section class="card card-front" aria-label="Card front">
    <svg class="bands" viewBox="0 0 320 540" preserveAspectRatio="none" aria-hidden="true">
      <path d="M0 330 C90 380 230 360 320 270 L320 540 L0 540 Z" fill="var(--band-1)"/>
      <path d="M0 410 C110 400 240 360 320 330 L320 540 L0 540 Z" fill="var(--band-2)"/>
    </svg>

    <div class="front-brand">
      <span class="brand-mark"></span>
      <span class="brand-name">FALCRIDGE HIRES</span>
    </div>

    <div class="person">
      <p class="person-name"><span class="first">Dwight</span> <span class="last">Penner</span></p>
      <p class="person-title">CFO</p>
      <div class="contact-icons">
        <svg viewBox="0 0 26 26" aria-label="Phone"><circle cx="13" cy="13" r="13" fill="var(--orange)"/><path d="M9 7.5c.6-.4 1.2-.2 1.5.3l1 1.8c.3.5.1 1-.3 1.3l-.7.5c.6 1.4 1.6 2.4 3 3l.5-.7c.3-.4.9-.6 1.3-.3l1.8 1c.5.3.7.9.3 1.5l-.7.9c-.5.6-1.4.8-2.2.5-3-1.2-5.3-3.5-6.5-6.5-.3-.8-.1-1.7.5-2.2z" fill="var(--white)"/></svg>
        <svg viewBox="0 0 26 26" aria-label="Email"><circle cx="13" cy="13" r="13" fill="var(--orange)"/><rect x="7" y="8.5" width="12" height="9" rx="1" fill="none" stroke="var(--white)" stroke-width="1.4"/><path d="M7.5 9.5 13 13.5 18.5 9.5" fill="none" stroke="var(--white)" stroke-width="1.4"/></svg>
        <svg viewBox="0 0 26 26" aria-label="Website"><circle cx="13" cy="13" r="13" fill="var(--orange)"/><circle cx="13" cy="13" r="6" fill="none" stroke="var(--white)" stroke-width="1.3"/><ellipse cx="13" cy="13" rx="2.6" ry="6" fill="none" stroke="var(--white)" stroke-width="1.1"/><path d="M7 13h12" stroke="var(--white)" stroke-width="1.1"/></svg>
      </div>
      <div class="contact-lines">
        <p>555 318-0476</p>
        <p>info@website.com</p>
        <p>www.website.com</p>
      </div>
    </div>

    <ul class="services">
      <li>Weddings</li><li>Concerts</li><li>Events</li><br>
      <li>Charity</li><li>Sporting and Corp</li><br>
      <li>Luxury Restroom Trailers Rental and Sales</li>
    </ul>
  </section>
</main>
</body>
</html>
```